Clinic for cellulit and fat removal

Name of clinic :
Lirava
- Body & Health (this has to be written on the site.)
I need CMS for me to be able to make changes myself.
A webpage for woman searching for a solution to remove fat and cellulit.
The owner is a brazilian woman in Denmark, and want her sense of aestetic shines thru the website.
There needs to be a slide show on the landing page showing big sliding pictures, of the clinic and and the treatments.
The Cryolipolysis, is a treatment freezing fat and cellulit, and this treatment will be the Attraction of the clinic.
Needs These pages in a horisontal fasion. (written in Danish)
Lirava
Behandlinger
- Cryolipolysis
- Trimflox
- Lymfemassage
- Korathelix
- Amberline Tide
Produkter
Priser
Kontakt
Clinic
Coded - Design and coding required
5+ page

```html
<!DOCTYPE html>
<html lang="en">
<head>
<meta charset="utf-8">
<title>Lirava – Body &amp; Health</title>
<link rel="stylesheet" href="https://fonts.googleapis.com/css2?family=Roboto:wght@300;400;500;700&family=Roboto+Slab:wght@300;400&display=swap">
<style>
:root{
  --green:#a6c93a;
  --ink:#4a4a4a;
  --muted:#777;
  --light:#f4f5f7;
  --line:#e3e3e3;
  --footer-bar:#4d4d4d;
  --white:#fff;
}
*{box-sizing:border-box;margin:0;padding:0}
html,body{width:669px;height:1200px;overflow:hidden;background:var(--white)}
body{position:relative;font-family:"Roboto",Arial,sans-serif;color:var(--ink)}
.abs{position:absolute}
/* header */
.site-header{position:absolute;left:0;top:0;width:669px;height:56px;background:var(--white)}
.logo{left:48px;top:14px;font-family:"Roboto Slab",Georgia,serif;font-weight:300;font-size:22px;color:#555}
.nav{left:286px;top:25px;display:flex;font-size:6.5px;letter-spacing:.2px;font-weight:500}
.nav a{color:#555;text-decoration:none;margin-right:27px}
.nav a.active{color:var(--green)}
.lang{left:566px;top:18px;width:55px;height:22px;border:1px solid #ccc;border-radius:2px;font-size:6px;display:flex;align-items:center;padding-left:5px;gap:4px;color:#333}
.lang .flag{width:9px;height:6px;background:#3a4f8c}
/* hero */
.hero{left:0;top:56px;width:669px;height:276px;background:linear-gradient(100deg,#e8c6b0 0%,#efe2d8 35%,#f3eeea 60%,#e6e2e0 100%)}
.hero-title{left:46px;top:150px;color:var(--white);font-weight:500;line-height:1}
.hero-title .small{font-size:21px;display:block}
.hero-title .big{font-size:27px;display:block;margin-top:6px}
.dots{left:47px;top:316px;display:flex;gap:3px}
.dots span{width:7px;height:7px;border:1px solid var(--white);border-radius:50%}
.dots span.on{border-color:var(--green)}
/* band */
.band{left:0;top:332px;width:669px;height:65px;background:var(--green);color:var(--white);text-align:center}
.band h2{font-size:13.5px;font-weight:500;margin-top:16px}
.band p{font-size:11.5px;margin-top:5px;font-weight:300}
/* common */
.section-title{font-size:14px;font-weight:400;color:#444}
.copy{font-size:6.3px;line-height:14.4px;color:var(--muted)}
.btn-solid{background:var(--green);color:var(--white);font-size:7.5px;font-weight:500;display:flex;align-items:center;justify-content:center;border-radius:2px}
.btn-line{border:1px solid var(--green);color:var(--green);font-size:7.5px;font-weight:500;display:flex;align-items:center;justify-content:center;border-radius:2px}
.video{left:362px;top:434px;width:259px;height:157px;background:linear-gradient(135deg,#eef3f8,#c8d9ec 70%,#b6cde6)}
/* services */
.services{left:0;top:624px;width:669px;height:202px;background:var(--light)}
.service{width:100px;text-align:center}
.service .pic{width:84px;height:84px;border-radius:50%;border:4px solid #e4e4e4;margin:0 auto}
.service .label{font-size:8.3px;font-weight:400;margin-top:12px;color:#444}
/* testimonial */
.avatar{left:285px;top:879px;width:70px;height:70px;border-radius:50%;background:linear-gradient(160deg,#b98a6a,#d9b59a)}
/* footer */
.footer{left:0;top:1011px;width:669px;height:151px;background:var(--light)}
.f-head{font-size:8.5px;font-weight:400;color:#444}
.f-list{list-style:none;font-size:6.4px;color:#666;line-height:14.4px}
.f-list li::before{content:"»";margin-right:10px;color:#888}
.contact{font-size:6.4px;color:#666}
.contact div{display:flex;gap:7px;margin-bottom:9px}
.contact svg{flex:none}
.email-box{border:1px solid #ccc;background:var(--white);width:118px;height:18px;font-size:6.5px;padding:5px 8px;color:#444}
.socials{display:flex;gap:4px}
.socials span{width:20px;height:20px;border:1px solid #aaa;border-radius:50%}
.bottom-bar{left:0;top:1162px;width:669px;height:38px;background:var(--footer-bar);color:var(--white);font-size:6.5px;text-align:center;line-height:38px}
</style>
</head>
<body>

<header class="site-header">
  <div class="abs logo">Lirava</div>
  <nav class="abs nav">
    <a class="active">LIRAVA</a><a>BEHANDLINGER</a><a>PRODUKTER</a><a>PRISER</a><a>KONTAKT</a>
  </nav>
  <div class="abs lang"><span class="flag"></span>English
    <svg width="6" height="4" viewBox="0 0 6 4" style="margin-left:6px"><path d="M0 0l3 3 3-3" fill="none" stroke="#333" stroke-width="1"/></svg>
  </div>
</header>

<section class="abs hero" role="img" aria-label="Slideshow photo: therapist performing a body treatment on a client in the clinic"></section>
<div class="abs hero-title"><span class="small">LIRAVA</span><span class="big">BODY &amp; HEALTH</span></div>
<div class="abs dots"><span></span><span class="on"></span><span></span></div>

<section class="abs band">
  <h2>THE CRYOLIPOLYSIS, IS A TREATMENT FREEZING</h2>
  <p>FAT&amp; CELLULIT, &amp; THIS TREATMENT WILL BE THE ATTRACTION OF THE CLINIC</p>
</section>

<h2 class="abs section-title" style="left:48px;top:420px">WELCOME TO LIRAVA</h2>
<p class="abs copy" style="left:48px;top:447px;width:290px">Sed ut perspiciatis unde omnis iste natus error sit voluptatem accusantium doloremque lau dantiu m, totam rem aperiam, eaque ipsa quae ab illo inventore veritatis et quasi architecto beatae vitae dicta sunt explicabo. Nemo enim ipsam voluptatem quia voluptas sit quia consequuntur magni dol ores eos qui ratione voluptatem sequi nesciunt</p>
<p class="abs copy" style="left:48px;top:512px;width:290px">Eaque ipsa quae ab illo inventore veritatis et quasi architecto beatae vitae dicta sunt explicabo. Nemo enim ipsam voluptatem quia voluptas sit quia consequuntur magni dol ores eos qui ratione veritatis et quasi architecto&nbsp; voluptatem sequi nesciunt</p>
<div class="abs btn-solid" style="left:48px;top:566px;width:78px;height:24px">READ MORE</div>
<div class="abs video" role="img" aria-label="Video preview: body contour treatment areas marked on a waist"></div>
<svg class="abs" style="left:477px;top:497px" width="30" height="30" viewBox="0 0 30 30" aria-hidden="true"><circle cx="15" cy="15" r="14" fill="#fff" fill-opacity=".85" stroke="#a6c93a" stroke-width="1.5"/><path d="M12 9.5l8 5.5-8 5.5z" fill="#a6c93a"/></svg>

<section class="abs services">
  <h2 class="abs section-title" style="left:0;width:669px;text-align:center;top:16px">OUR SERVICES</h2>
  <p class="abs copy" style="left:0;width:669px;text-align:center;top:36px">Sed ut perspiciatis unde omnis iste natus error sit voluptatem accusantium doloremque lau dantiu m, totam rem aperiam,</p>
  <div class="abs service" style="left:70px;top:72px"><div class="pic" role="img" aria-label="Cryolipolysis treatment photo" style="background:linear-gradient(135deg,#cfd8e6,#e9ecf1)"></div><div class="label">CRYOLIPOLYSIS</div></div>
  <div class="abs service" style="left:214px;top:72px"><div class="pic" role="img" aria-label="Trimflox treatment photo" style="background:linear-gradient(135deg,#dfe6ef,#f1e4dc)"></div><div class="label">TRIMFLOX</div></div>
  <div class="abs service" style="left:359px;top:72px"><div class="pic" role="img" aria-label="Lymph massage photo" style="background:linear-gradient(135deg,#efc7b2,#f6ddd0)"></div><div class="label">LYMFEMASSAGE</div></div>
  <div class="abs service" style="left:503px;top:72px"><div class="pic" role="img" aria-label="Korathelix relaxation treatment photo" style="background:linear-gradient(135deg,#e2cdbf,#f3ebe5)"></div><div class="label">KORATHELIX</div></div>
</section>

<h2 class="abs section-title" style="left:48px;top:846px">ABOUT US</h2>
<p class="abs copy" style="left:48px;top:873px;width:210px">Sed ut perspiciatis unde omnis iste natus error sit voluptatem accusan tium doloremque laudantium, totam rem aperiam, eaque ipsa quae ab illo inventore veritatis et quasi architecto beatae vitae dicta sunt expli-cabo. Nemo enim ipsam voluptatem quia voluptas sit aspernatur aut odit aut fugit, sed quia consequuntur magni dolores eos qui ratione voluptatem sequi nesciunt.</p>
<div class="abs btn-line" style="left:48px;top:966px;width:70px;height:22px">READ MORE</div>

<h2 class="abs section-title" style="left:285px;top:846px">TESTIMONIALS</h2>
<div class="abs avatar" role="img" aria-label="Client portrait"></div>
<div class="abs" style="left:366px;top:884px;font-size:16px;color:#666;font-family:Georgia,serif">&ldquo;</div>
<p class="abs copy" style="left:376px;top:891px;width:242px;line-height:13px">Sed ut perspiciatis unde omnis iste natus error sit voluptatem accusan tium dolo-remque laudantium, totam rem aperiam, eaque ipsa quae ab illo inventore verita-tis et quasi architecto beatae vitae dicta sunt explicabo. Nemo enim ipsam volup-magni dolores eos qui ratione voluptatem sequi nesciunt.</p>
<div class="abs" style="left:547px;top:935px;font-size:16px;color:#666;font-family:Georgia,serif">&rdquo;</div>
<div class="abs" style="left:377px;top:960px;font-size:7px;color:var(--green);font-weight:500">Name : Mira Dalsgaard</div>
<div class="abs" style="left:377px;top:972px;font-size:5.8px;color:#888">Posed on 02 April 2017</div>

<footer class="abs footer">
  <div class="abs f-head" style="left:70px;top:32px">QUICK LINKS</div>
  <ul class="abs f-list" style="left:72px;top:51px">
    <li>Lirava</li><li>Behandlinger</li><li>Produkter</li><li>Priser</li><li>Kontakt</li>
  </ul>
  <div class="abs f-head" style="left:193px;top:32px">CONTACT US</div>
  <div class="abs contact" style="left:194px;top:58px">
    <div><svg width="8" height="7" viewBox="0 0 8 7"><path d="M0 2h8v5H0z M1 0h6v2H1z" fill="#777"/></svg>(000)-343-5520 (Phone)</div>
    <div><svg width="8" height="7" viewBox="0 0 8 7"><rect y="2" width="8" height="5" fill="#777"/><rect x="2" width="4" height="2" fill="#777"/></svg>(000)-343-5520 (Fax)</div>
    <div><svg width="8" height="7" viewBox="0 0 8 7"><rect width="8" height="6" fill="#777"/><path d="M0 0l4 3 4-3" stroke="#fff" fill="none" stroke-width=".8"/></svg><span style="text-decoration:underline">info@lirava.dk</span></div>
    <div><svg width="8" height="8" viewBox="0 0 8 8"><path d="M4 0a3 3 0 0 1 3 3c0 2-3 5-3 5S1 5 1 3a3 3 0 0 1 3-3z" fill="#777"/><circle cx="4" cy="3" r="1" fill="#fff"/></svg><span>70 Lorem Ipsum Dummy Text<br>Lorem Ipsum</span></div>
  </div>
  <div class="abs f-head" style="left:347px;top:32px">NEWSLETTER</div>
  <p class="abs copy" style="left:347px;top:50px;width:120px;line-height:11px;color:#777">Register Your email address to get information abiout us</p>
  <div class="abs email-box" style="left:347px;top:88px">Email Address</div>
  <div class="abs btn-solid" style="left:348px;top:113px;width:45px;height:15px;font-size:5.6px">SUBSCRIBE</div>
  <div class="abs f-head" style="left:493px;top:33px">FOLLOW US</div>
  <p class="abs copy" style="left:493px;top:51px;width:110px;line-height:10.5px;font-size:5.8px;color:#888">Lorem ipsum dolor sit amet, conse ctetur adipiscing elit. Nulla in purus nibh. Donec ornare</p>
  <div class="abs socials" style="left:492px;top:99px"><span></span><span></span><span></span><span></span><span></span></div>
</footer>
<div class="abs bottom-bar">© Copyright 2017 Lirava.All Rights Reserved</div>

</body>
</html>
```